Dovecote Realty

Business cards for 4 people

They need to say for all
87 Tarrow Quay, Boston MA 02114

Each person will have their own personal information
We would like gold embossing for the name of the company
Marla is the blonde sitting in the chair smiling her information should be on the back of the card with her name and information
Should say for slogan classic pattern, elevated experience
grace@dovecoteprops.com
(413) 555-0182

Odette is the brunette with wavy hair in the tan suit odette@dovecoteprops.com
(617) 555-0137

faith@dovecoteprops.com
(413) 555-0164
standing next to the chair

hope@dovecoteprops.com
(413) 555-0199
close up headshot

```html
<!DOCTYPE html>
<html lang="en">
<head>
<meta charset="utf-8">
<title>Dovecote Realty — Business Cards</title>
<link rel="stylesheet" href="https://fonts.googleapis.com/css2?family=Open+Sans:wght@400;600;700&display=swap">
<style>
  :root {
    --bg: #222224;
    --card: #1c1c20;
    --card-edge: #141417;
    --gold: #e1a94f;
    --gold-light: #e8bf72;
    --white: #ffffff;
    --ink: #2a2118;
    --emboss: #2b2b30;
    --photo-light: #fbf8ee;
    --photo-mid: #a77b52;
    --photo-dark: #6e4c31;
  }
  * { box-sizing: border-box; margin: 0; padding: 0; }
  html, body { width: 1200px; height: 780px; overflow: hidden; }
  body {
    background: var(--bg);
    font-family: "Open Sans", sans-serif;
    position: relative;
  }
  .card {
    position: absolute;
    top: 235px;
    width: 540px;
    height: 310px;
    background: var(--card);
    border-radius: 3px;
    box-shadow: 0 4px 0 var(--card-edge), 0 8px 0 #18181b, 0 22px 40px rgba(0,0,0,.55);
    overflow: hidden;
  }
  .card-front { left: 40px; }
  .card-back { left: 620px; }

  /* Front */
  .brand {
    position: absolute;
    top: 30px;
    left: 150px;
    display: flex;
    align-items: center;
    gap: 10px;
  }
  .brand-name {
    color: var(--gold);
    font-weight: 600;
    font-size: 15px;
    letter-spacing: 2px;
    text-transform: uppercase;
    white-space: nowrap;
  }
  .brand-circle {
    width: 42px; height: 42px;
    border: 2px solid var(--gold);
    border-radius: 50%;
    flex: none;
  }
  .name-band {
    position: absolute;
    top: 92px;
    left: 0;
    width: 330px;
    height: 60px;
    padding: 6px 0 0 18px;
    background: linear-gradient(90deg, var(--gold-light) 0%, #c99a55 35%, rgba(120,95,60,.55) 70%, rgba(28,28,32,0) 100%);
  }
  .person-name {
    color: var(--white);
    font-weight: 700;
    font-size: 27px;
    line-height: 1.1;
    white-space: nowrap;
  }
  .person-title {
    color: var(--ink);
    font-size: 11px;
    margin-top: 2px;
    white-space: nowrap;
  }
  .contact {
    position: absolute;
    top: 170px;
    left: 18px;
    color: var(--gold);
    font-size: 14px;
    line-height: 1.35;
    list-style: none;
  }
  .contact li { display: flex; align-items: center; gap: 7px; white-space: nowrap; }
  .contact .address { padding-left: 21px; }
  .contact svg { width: 14px; height: 14px; flex: none; }
  .portrait {
    position: absolute;
    top: 118px;
    left: 355px;
    width: 170px;
    height: 170px;
    border-radius: 50%;
    border: 4px solid var(--gold);
    background: linear-gradient(200deg, var(--photo-light) 0%, var(--photo-light) 30%, var(--photo-mid) 60%, var(--photo-dark) 100%);
  }

  /* Back */
  .back-brand {
    position: absolute;
    inset: 0;
    display: flex;
    align-items: center;
    justify-content: center;
    gap: 18px;
  }
  .back-brand .brand-name {
    color: var(--emboss);
    font-size: 30px;
    letter-spacing: 4px;
  }
  .back-brand .brand-circle {
    width: 84px; height: 84px;
    border: 3px solid var(--emboss);
  }
</style>
</head>
<body>

<section class="card card-front">
  <div class="brand">
    <span class="brand-name">Dovecote Realty</span>
    <span class="brand-circle"></span>
  </div>

  <div class="name-band">
    <h1 class="person-name">Odette Lamarche</h1>
    <p class="person-title">Real Estate Advisor and Sales Manager</p>
  </div>

  <ul class="contact">
    <li class="address">87 Tarrow Quay,</li>
    <li class="address">Boston MA 02114</li>
    <li>
      <svg viewBox="0 0 16 16" aria-hidden="true"><path fill="currentColor" d="M3.6 1.5l2.2 2.6-1.3 1.6c.9 2 2.6 3.7 4.6 4.6l1.6-1.3 2.6 2.2-1.2 2.2C7.3 14.7 1.6 9 1.4 2.7z"/></svg>
      (617) 555-0137
    </li>
    <li>
      <svg viewBox="0 0 16 16" aria-hidden="true"><circle cx="8" cy="8" r="6.3" fill="none" stroke="currentColor" stroke-width="1.4"/><ellipse cx="8" cy="8" rx="2.6" ry="6.3" fill="none" stroke="currentColor" stroke-width="1.2"/><path d="M1.8 8h12.4" stroke="currentColor" stroke-width="1.2"/></svg>
      www.dovecoteprops.com
    </li>
    <li>
      <svg viewBox="0 0 16 16" aria-hidden="true"><rect x="1.5" y="3.5" width="13" height="9" fill="none" stroke="currentColor" stroke-width="1.4"/><path d="M1.5 3.5L8 9l6.5-5.5" fill="none" stroke="currentColor" stroke-width="1.4"/></svg>
      odette@dovecoteprops.com
    </li>
  </ul>

  <div class="portrait" role="img" aria-label="Portrait photo of Odette, brunette with wavy hair in a tan suit"></div>
</section>

<section class="card card-back">
  <div class="back-brand">
    <span class="brand-name">Dovecote Realty</span>
    <span class="brand-circle"></span>
  </div>
</section>

</body>
</html>
```